MRT Property - Business Cards

Looking for a business card & general letterhead, signage etc design for our new logo.

Colours:
000a20
0056a2
00b5ef
0088ce
68cef2

Fonts:
Poppins
Karla

Please keep look and feel of new brand - example in the zip package I sent.

```html
<!DOCTYPE html>
<html lang="en">
<head>
<meta charset="utf-8">
<title>MRT Property – Business Cards</title>
<link href="https://fonts.googleapis.com/css2?family=Poppins:wght@300;400;800&display=swap" rel="stylesheet">
<style>
  :root {
    --navy: #000a20;
    --card-navy: #0a1128;
    --brand-blue: #0056a2;
    --cyan: #00b5ef;
    --mid-blue: #0088ce;
    --light-blue: #68cef2;
    --pattern-violet: #4a5bc4;
    --white: #ffffff;
    --backdrop: #1b1c20;
  }
  * { margin: 0; padding: 0; box-sizing: border-box; }
  html, body {
    width: 1200px; height: 900px; overflow: hidden;
    background: var(--backdrop);
    font-family: "Poppins", sans-serif;
  }
  .card {
    position: absolute; top: 290px;
    width: 560px; height: 320px;
    border-radius: 24px; overflow: hidden;
    background: var(--card-navy);
    box-shadow: 0 20px 50px rgba(0,0,0,.55);
  }
  .card--front { left: 25px; }
  .card--back { left: 615px; }

  /* front */
  .card-top {
    position: absolute; left: 0; top: 0; width: 100%; height: 180px;
    background: var(--white);
    border-bottom: 2px solid var(--cyan);
    display: flex; align-items: center; justify-content: center;
  }
  .brand-name {
    display: flex; align-items: center; gap: 12px;
    color: var(--brand-blue);
    font-weight: 800; font-size: 40px; line-height: 1;
  }
  .brand-dot {
    width: 16px; height: 16px; border-radius: 50%;
    background: var(--cyan);
  }
  .card-bottom {
    position: absolute; left: 0; top: 182px; width: 100%; height: 138px;
  }
  .holder {
    position: absolute; left: 40px; top: 42px; width: 200px;
  }
  .holder-name {
    color: var(--cyan); font-weight: 800; font-size: 24px;
    text-transform: uppercase; line-height: 1; white-space: nowrap;
  }
  .holder-title {
    color: var(--white); font-weight: 300; font-size: 13px; margin-top: 8px;
  }
  .divider {
    position: absolute; left: 250px; top: 16px;
    width: 1.5px; height: 106px; background: var(--mid-blue);
  }
  .contact-list {
    position: absolute; left: 268px; top: 13px;
    list-style: none; color: var(--white);
    font-weight: 400; font-size: 13.5px; line-height: 22px; white-space: nowrap;
  }
  .contact-list li { display: flex; align-items: center; gap: 6px; }
  .contact-list svg { width: 11px; height: 11px; flex: none; }

  /* back */
  .back-pattern {
    position: absolute; inset: 0;
    background: linear-gradient(215deg, var(--pattern-violet) 0%, #27306e 40%, var(--card-navy) 80%);
  }
  .back-brand {
    position: absolute; right: 34px; bottom: 34px;
    display: flex; align-items: center; gap: 10px;
    color: var(--white);
    font-weight: 800; font-size: 28px; line-height: 1;
  }
  .back-brand .brand-dot { width: 12px; height: 12px; }
</style>
</head>
<body>
  <article class="card card--front">
    <header class="card-top">
      <div class="brand-name"><span class="brand-dot"></span>MRT Property</div>
    </header>
    <section class="card-bottom">
      <div class="holder">
        <h1 class="holder-name">Dana Hollis</h1>
        <p class="holder-title">Founder &amp; Principal</p>
      </div>
      <div class="divider"></div>
      <ul class="contact-list">
        <li>
          <svg viewBox="0 0 16 16" aria-hidden="true"><path d="M4 1l3 3-2 2c1 2 3 4 5 5l2-2 3 3-2 3C7 15 1 9 1 3z" fill="var(--cyan)"/></svg>
          +1- 555-014-2290
        </li>
        <li>
          <svg viewBox="0 0 16 16" aria-hidden="true"><rect x="1" y="3" width="14" height="10" fill="none" stroke="var(--cyan)" stroke-width="1.5"/><path d="M1 3l7 6 7-6" fill="none" stroke="var(--cyan)" stroke-width="1.5"/></svg>
          info@mrtproperty.com
        </li>
        <li>
          <svg viewBox="0 0 16 16" aria-hidden="true"><circle cx="8" cy="8" r="7" fill="none" stroke="var(--cyan)" stroke-width="1.5"/><path d="M1 8h14M8 1c-3 4-3 10 0 14M8 1c3 4 3 10 0 14" fill="none" stroke="var(--cyan)" stroke-width="1.2"/></svg>
          www.mrtproperty.com
        </li>
        <li>4120 Harbor View Road</li>
        <li>#12, Suite Lakewood Park</li>
      </ul>
    </section>
  </article>

  <article class="card card--back">
    <div class="back-pattern" role="img" aria-label="Repeating brand pattern in violet and navy tones"></div>
    <div class="back-brand"><span class="brand-dot"></span>MRT Property</div>
  </article>
</body>
</html>
```